Marlowe Group needs a business card

I would like the card to be simple but modern and elegant.
I like black and white.
or black and gold.
we are a private finance lender and also are involved in property and property developments.

please look at the business card photos i provided i would like M.G only one one side and all the other details on the other side use fonts that tie in with my theme.

Industry/Entity Type

Finance

Contact Information for Business Card

Marlowe Group (M.G) Daniel Marlowe M: 0413586207 E: danmarl@inboxmail.test

Font styles to use
Other font styles liked:
• Use fonts that would reflect our business

Colors
000000
ffffff

Requirements
Must have
• one side of details
• other side has either M.G or Marlowe Group like in the photos provided

```html
<!DOCTYPE html>
<html lang="en">
<head>
<meta charset="utf-8">
<title>Marlowe Group — Business Card</title>
<link rel="stylesheet" href="https://fonts.googleapis.com/css2?family=Open+Sans:wght@400&family=Tinos:ital@0;1&display=swap">
<style>
  :root {
    --ink: #000000;
    --card-black: #03030c;
    --paper: #ffffff;
    --backdrop: #e6e4e0;
    --serif: "Tinos", "Times New Roman", serif;
    --sans: "Open Sans", Arial, sans-serif;
  }
  html, body {
    margin: 0;
    padding: 0;
    width: 1200px;
    height: 1200px;
    overflow: hidden;
    background: var(--backdrop);
  }
  .canvas {
    position: relative;
    width: 1200px;
    height: 1200px;
  }
  .card {
    position: absolute;
    left: 232px;
    width: 735px;
    height: 415px;
    box-sizing: border-box;
  }
  .card--front {
    top: 159px;
    background: var(--card-black);
    display: flex;
    align-items: center;
    justify-content: center;
  }
  .monogram {
    font-family: var(--serif);
    font-weight: 400;
    font-size: 145px;
    line-height: 1;
    color: var(--paper);
    letter-spacing: -2px;
    margin: 0;
  }
  .card--back {
    top: 624px;
    background: var(--paper);
    color: var(--ink);
  }
  .company-name {
    position: absolute;
    right: 35px;
    top: 24px;
    margin: 0;
    font-family: var(--serif);
    font-style: italic;
    font-weight: 400;
    font-size: 27px;
    line-height: 1;
  }
  .person-name {
    position: absolute;
    left: 45px;
    top: 297px;
    margin: 0;
    font-family: var(--sans);
    font-size: 22px;
    line-height: 1;
    letter-spacing: 0.3px;
  }
  .name-rule {
    position: absolute;
    left: 45px;
    top: 331px;
    width: 95px;
    height: 1.5px;
    background: var(--ink);
  }
  .contact {
    position: absolute;
    top: 352px;
    display: flex;
    align-items: center;
    gap: 8px;
    margin: 0;
    font-family: var(--sans);
    font-size: 20px;
    line-height: 1;
  }
  .contact--phone { left: 45px; }
  .contact--email { left: 250px; }
  .contact-icon { display: block; }
</style>
</head>
<body>
<main class="canvas">
  <section class="card card--front" aria-label="Card front">
    <p class="monogram">M.G</p>
  </section>

  <section class="card card--back" aria-label="Card back">
    <p class="company-name">Marlowe Group</p>
    <p class="person-name">Daniel Marlowe</p>
    <div class="name-rule"></div>
    <p class="contact contact--phone">
      <svg class="contact-icon" width="11" height="17" viewBox="0 0 11 17" aria-hidden="true">
        <rect x="1" y="1" width="9" height="15" rx="1.5" fill="none" stroke="#000" stroke-width="2"/>
        <rect x="3" y="12.5" width="5" height="1.5" fill="#000"/>
      </svg>
      <span>0413586207</span>
    </p>
    <p class="contact contact--email">
      <svg class="contact-icon" width="20" height="15" viewBox="0 0 20 15" aria-hidden="true">
        <rect x="1" y="1" width="18" height="13" fill="none" stroke="#000" stroke-width="1.8"/>
        <path d="M1 1 L10 8.5 L19 1 M1 14 L7.5 7 M19 14 L12.5 7" fill="none" stroke="#000" stroke-width="1.6"/>
      </svg>
      <span>danmarl@inboxmail.test</span>
    </p>
  </section>
</main>
</body>
</html>
```